Design my site www.brieflyledger.com

So here is what I am thinking in terms of design:

https://plenvo.com

https://www.skyluxair.com

http://kalvex.com/harbor-plaza-tower/

I want the theme to be white and blue (royal blue). I attached a paint picture of what I would like the site to look like in terms of placing the text. Generally, what I like about the sites above is that they are simple, you can navigate easily and have some kind of idea of what's going on by looking at the center (picture and motto). Let's establish a clear understanding of how the functional part of the site would look like. Please see the picture attached.

I want to keep it simple: On top would be the Name 'BRIEFLY ledger", somewhere to the right on top on the page would be 'Sign in" button.

In the center would be a picture (maybe a video) with the Motto (on top of it all in capital) OBSERVE NAVIGATE DECIDE and below would be the "sign up now"

Below the picture (like on kalvex.com site) or to the left on top of the page would be "About Us', "Press" "Contact Us' buttons.

Then once the user gets to his page his got 3 tabs " Press Headlines", "Events", " Briefings".

we would keep the same format I only have on the site, but separate for every Tab.

I do not want the user to get distracted. I also want him to be able to access the page though mobile phone and be able to get automatic updates just like Zorvan Pings without having to sign in daily.

The landing page must be minimalist yet with business/corporate feel where users can navigate easily and a "what you see is what you get" approach. You want an image or video (personally I prefer the video.. it does capture the users attention instantly, as long as it is an interesting video), with your taglines in it.

Sections available to public: About Us, Contact Us, Landing Page with Signup Option

Private: Public Sections + User Account Page, Tabs for (Events, Press Headlines, Briefings)

Target Market(s)

PR/media monitoring/diplomatic community

Coding

Coded - Design and coding required

Number of Pages Required

1 page

Font styles to use
Serif
Sans Serif

Colors
0255a3
ec1f27

Requirements
Must have
• a simple landing page, that is user friendly.
Nice to have
• a video with the explanation of how to navigate the site
Should not have
• too many colors, graphs etc.

```html
<!DOCTYPE html>
<html lang="en">
<head>
<meta charset="utf-8">
<title>Briefly Ledger</title>
<link rel="stylesheet" href="https://fonts.googleapis.com/css2?family=Roboto:wght@300;400;500;700&display=swap">
<style>
  :root {
    --royal-blue: #0255a3;
    --signal-red: #ec1f27;
    --white: #ffffff;
    --hamburger-bg: #f4f4f4;
    --divider: #e2e2e2;
    --nav-light: #2481dc;
    --nav-active: #0a4690;
    --nav-active-deep: #06346c;
    --hero-dark: #121a2a;
    --hero-mid: #3a3c40;
    --hero-warm: #6b5a44;
  }
  * { box-sizing: border-box; margin: 0; padding: 0; }
  html, body { width: 1200px; height: 716px; overflow: hidden; background: var(--white); }
  body { font-family: "Roboto", Arial, sans-serif; position: relative; }

  .site-header {
    position: absolute; top: 0; left: 0; width: 1200px; height: 61px;
    background: var(--white); display: flex; align-items: stretch;
  }
  .menu-toggle {
    width: 69px; background: var(--hamburger-bg); border-right: 1px solid var(--divider);
    display: flex; align-items: center; justify-content: center;
  }
  .brand {
    flex: 1; display: flex; align-items: center; padding-left: 23px;
    font-weight: 700; font-size: 21px; letter-spacing: 0.3px; color: var(--royal-blue);
  }
  .social-links {
    width: 189px; border-left: 1px solid var(--divider); background: #f7f7f7;
    display: flex; align-items: center; justify-content: center; gap: 2px;
  }
  .social-links span { width: 29px; height: 29px; background: var(--royal-blue); display: block; }
  .social-links span:nth-child(4) { background: #d14836; }
  .social-links span:nth-child(5) { background: #1d7fb6; }
  .sign-in {
    width: 129px; background: var(--royal-blue); color: var(--white);
    display: flex; align-items: center; justify-content: center;
    font-size: 14px; font-weight: 500; letter-spacing: 0.3px;
  }

  .hero {
    position: absolute; top: 61px; left: 0; width: 1200px; height: 594px; overflow: hidden;
  }
  .hero-photo {
    position: absolute; inset: 0;
    background:
      radial-gradient(ellipse at 50% 55%, rgba(90,80,66,0.55), transparent 65%),
      linear-gradient(160deg, var(--hero-dark) 0%, var(--hero-mid) 45%, var(--hero-warm) 100%);
  }
  .hero-shade { position: absolute; inset: 0; background: rgba(10,18,36,0.35); }
  .hero-content {
    position: absolute; inset: 0; text-align: center; color: var(--white);
  }
  .hero-mark {
    position: absolute; left: 575px; top: 194px; width: 50px; height: 50px;
    border: 3px solid var(--white); border-radius: 6px;
  }
  .hero-label {
    position: absolute; top: 260px; left: 0; width: 100%; height: 24px;
    display: flex; align-items: center; justify-content: center; gap: 12px;
    font-size: 20px; font-weight: 400; letter-spacing: 0.3px; line-height: 24px;
  }
  .hero-label::before, .hero-label::after {
    content: ""; width: 99px; height: 2px; background: var(--signal-red);
  }
  .motto {
    position: absolute; top: 296px; left: 0; width: 100%; height: 70px;
    font-size: 68px; font-weight: 300; letter-spacing: 0.5px; line-height: 70px;
    white-space: nowrap;
  }
  .hero-cta {
    position: absolute; top: 389px; left: 511px; width: 178px; height: 38px;
    border: 1px solid rgba(255,255,255,0.55);
    display: flex; align-items: center; justify-content: center;
    font-size: 14px; font-weight: 500; letter-spacing: 0.3px; color: var(--white);
  }

  .section-nav {
    position: absolute; top: 655px; left: 0; width: 1200px; height: 61px; display: flex;
  }
  .section-link {
    flex: 1; display: flex; align-items: center; justify-content: center; gap: 16px;
    background: var(--nav-light); color: var(--white);
    font-size: 19px; font-weight: 500; letter-spacing: 0.3px;
  }
  .section-link + .section-link { border-left: 1px solid rgba(0,0,0,0.25); }
  .section-link.is-active {
    background: radial-gradient(ellipse at 50% 50%, var(--nav-active) 40%, var(--nav-active-deep) 100%);
  }
  .section-link svg { width: 34px; height: 34px; }
</style>
</head>
<body>
  <header class="site-header">
    <div class="menu-toggle">
      <svg width="24" height="14" viewBox="0 0 24 14" aria-hidden="true">
        <rect y="0" width="24" height="2.5" fill="#ec1f27"/>
        <rect y="5.5" width="24" height="2.5" fill="#ec1f27"/>
        <rect y="11" width="24" height="2.5" fill="#ec1f27"/>
      </svg>
    </div>
    <div class="brand">BRIEFLY LEDGER</div>
    <nav class="social-links" aria-label="Social profiles">
      <span></span><span></span><span></span><span></span><span></span>
    </nav>
    <a class="sign-in">SIGN IN</a>
  </header>

  <section class="hero">
    <div class="hero-photo" role="img" aria-label="Aerial photograph of a dense downtown skyline with office towers"></div>
    <div class="hero-shade"></div>
    <div class="hero-content">
      <div class="hero-mark" aria-hidden="true"></div>
      <div class="hero-label">BRIEFLY LEDGER</div>
      <h1 class="motto">OBSERVE • NAVIGATE • DECIDE</h1>
      <a class="hero-cta">SIGN UP NOW</a>
    </div>
  </section>

  <nav class="section-nav">
    <a class="section-link">
      <svg viewBox="0 0 34 34" aria-hidden="true" fill="none" stroke="#fff" stroke-width="2">
        <circle cx="17" cy="17" r="15.5"/>
        <circle cx="17" cy="13" r="5"/>
        <path d="M8 27c2-5 5.5-7 9-7s7 2 9 7"/>
      </svg>
      ABOUT US
    </a>
    <a class="section-link is-active">
      <svg viewBox="0 0 34 34" aria-hidden="true" fill="none" stroke="#fff" stroke-width="2">
        <rect x="5" y="7" width="27" height="21" rx="2"/>
        <path d="M5 11H2v15a2 2 0 0 0 4 0"/>
        <rect x="9" y="11" width="9" height="5" fill="#fff" stroke="none"/>
        <path d="M21 12h7M21 16h7M9 20h19M9 24h19"/>
      </svg>
      PRESS
    </a>
    <a class="section-link">
      <svg viewBox="0 0 34 34" aria-hidden="true" fill="#fff">
        <rect x="3" y="4" width="5" height="26"/>
        <rect x="10" y="4" width="20" height="26"/>
        <circle cx="20" cy="14" r="4" fill="#2481dc"/>
        <path d="M13 26c1-5 4-7 7-7s6 2 7 7z" fill="#2481dc"/>
      </svg>
      CONTACT US
    </a>
  </nav>
</body>
</html>
```